Companybrochure for Consulting & Financing Firm

I need to have a Company Brochure asap for our company. We have a website that describes what we do, but we need also a brochure, that can be sent by PDF of eventually be printed as well.

The brochure should be short but nice and appealing to the customers.

We provide professional management consulting and help our customers to get finance for very diferent projects. Our business has a lot to do with personal relations, but also we are very professional in the way we work and how develop the solutions for our clients. Our clients are mainly government-owned firm, but also private trading companies and wealthy private investors.

Our customers are mainly in Latin America, but the company is headquater is in Switzerland. We are opening offices in Panama and Caracas, this should be easaly be adabtable later.

Please have a look at our website www.vorelpartners.ch. In the brochure, we would segment our services in 1.) Project Developments 2.) Management Conulting 3.) Investment Management and 4.) Finance Solutions.

Also do have a look at www.vorelpartners.ch
(Click E for the English version)
Updates

I managed to put the Mock-Up to the Website.
It is actually not really a mock-up, it is a version I have designed myself.
Well as I am not a designer, I hope you can make it much better.
The content however is what I would put in any other design as well.

Target Market(s)

Top Management, Investors, Entrepreneurs, Government Officials

Industry/Entity Type

Management Consulting

Requirements
Must have
• Design should reflect this image elements:

We are entrepreneurs.
We are comitted to get things done.
We work closely with the client side by side.
We are a professional partner.
We are not afraid of delivering unconventional solutions.
We look at the problem from various angles.
We analyse, develop solutions and implent results.
Should not have
• Typical US-American style elements. We do not want to give the impression of being a US company.

We do not want to appear to be neo-liberal. We are a politically neutral professional consulting firm.

```html
<!DOCTYPE html>
<html lang="en">
<head>
<meta charset="utf-8">
<title>Vorel Partners AG – Finance Solution</title>
<link rel="stylesheet" href="https://fonts.googleapis.com/css2?family=Inter+Tight:wght@300;400;600;700;800&display=swap">
<style>
  :root {
    --paper: #ffffff;
    --ink: #1c1c1c;
    --logo-grey: #333333;
    --accent-blue: #4a7bbd;
    --box-blue: #4d7dbd;
    --navy-deep: #0a1240;
    --navy: #12227a;
    --bar-black: #1a1a1a;
    --soft-white: #eef2fa;
  }
  * { box-sizing: border-box; margin: 0; padding: 0; }
  html, body {
    width: 1200px; height: 860px; overflow: hidden;
    background: var(--paper);
  }
  body {
    font-family: "Inter Tight", Arial, sans-serif;
    color: var(--ink);
  }
  .page { position: relative; width: 1200px; height: 860px; }

  .top-rule {
    position: absolute; left: 0; top: 44px; width: 100%; height: 11px;
    background: var(--bar-black);
  }

  .brand-name {
    position: absolute; right: 32px; top: 108px;
    font-size: 44px; font-weight: 700; letter-spacing: -0.5px;
    color: var(--logo-grey); line-height: 1;
  }

  .hero {
    position: absolute; left: 0; top: 184px; width: 1200px; height: 274px;
    overflow: hidden;
  }
  .hero-visual {
    position: absolute; inset: 0;
    background:
      linear-gradient(90deg, rgba(10,18,64,0) 40%, rgba(170,180,200,0.35) 62%, rgba(10,18,64,0) 82%),
      linear-gradient(100deg, #3a3a3a 0%, var(--navy) 18%, var(--navy-deep) 45%, #1d3a8a 60%, var(--navy-deep) 78%, var(--navy) 100%);
  }
  .hero-bands { position: absolute; inset: 0; }
  .hero-title {
    position: absolute; left: 66px; top: 122px;
    color: var(--paper); line-height: 0.82; letter-spacing: -5px;
    text-transform: uppercase;
  }
  .hero-title .line-light { display: block; font-size: 74px; font-weight: 300; padding-left: 10px; }
  .hero-title .line-bold { display: block; font-size: 74px; font-weight: 800; }

  .intro {
    position: absolute; left: 68px; top: 494px; width: 690px;
  }
  .intro-lead {
    color: var(--accent-blue); font-size: 21px; font-weight: 700;
    line-height: 27px; margin-bottom: 12px; width: 640px;
  }
  .intro-body {
    font-size: 18px; font-weight: 700; line-height: 23px;
    margin-bottom: 23px; letter-spacing: 0.1px;
  }
  .intro-body.narrow { width: 600px; }

  .testimonials {
    position: absolute; left: 733px; top: 492px; width: 433px; height: 316px;
    background: var(--box-blue);
  }
  .testimonials-head {
    position: relative; height: 46px; background: var(--bar-black);
    color: var(--paper); font-size: 17px; font-weight: 700;
    display: flex; align-items: center; justify-content: center;
    text-transform: uppercase; letter-spacing: 0.2px;
  }
  .testimonials-head svg { position: absolute; left: 0; top: 0; }
  .testimonials-body {
    padding: 22px 24px 0 14px;
    color: var(--soft-white); font-size: 15.2px; font-weight: 400;
    line-height: 23px; text-align: justify; letter-spacing: 0.15px;
  }
</style>
</head>
<body>
<div class="page">
  <div class="top-rule"></div>

  <div class="brand-name">Vorel Partners AG</div>

  <section class="hero">
    <div class="hero-visual" role="img" aria-label="Photograph of a butterfly resting on a flower in blue and grey tones, cut by diagonal bands"></div>
    <svg class="hero-bands" width="1200" height="274" viewBox="0 0 1200 274" aria-hidden="true">
      <polygon points="0,0 150,0 0,230" fill="#5a5a5a" opacity="0.55"/>
      <polygon points="640,0 880,0 700,274 460,274" fill="#c9ced8" opacity="0.22"/>
      <polygon points="960,0 1200,0 1200,120 1020,274 840,274" fill="#0f1f78" opacity="0.45"/>
    </svg>
    <h1 class="hero-title">
      <span class="line-light">Finance</span>
      <span class="line-bold">Solution</span>
    </h1>
  </section>

  <section class="intro">
    <p class="intro-lead">Financing growth opportunities sometimes calls for an entrepreneurial perspective, which is often not found in the traditional banking world.</p>
    <p class="intro-body">That is why we have committed ourselves to developing financing solutions for unconventional requirements. To do so, we often work with partners with complementary subject matter expertise and geographical coverage.</p>
    <p class="intro-body narrow">This gives us the flexibility to create innovative solutions – solutions that meet our clients' special needs.</p>
  </section>

  <aside class="testimonials">
    <h2 class="testimonials-head">
      <svg width="30" height="20" viewBox="0 0 30 20" aria-hidden="true"><polygon points="0,0 30,0 0,20" fill="var(--box-blue)"/></svg>
      What our clients have to say...
    </h2>
    <p class="testimonials-body">Lorem Ipsum is simply dummy text of the printing and typesetting industry. Lorem Ipsum has been the industry's standard dummy text ever since the 1500s, when an unknown printer took a galley of type and scrambled it to make a type specimen book. It has survived not only five centuries, but also the leap into electronic typesetting, remaining essentially unchanged. It was popularised in the 1960s with the release of Typeline sheets containing Lorem Ipsum passages, and more recently with desktop publishing software like</p>
  </aside>
</div>
</body>
</html>
```